Coffeeshop menu for filter tip

We want to have a cannabis (coffeeshop) menu in the size 25mm wide x 60mm wide. Some examples attached.

it must have the following text:
Menu

WEED p/g
Oblivane €16
Cloudplum €14
Tide Runner €14
Quincefig €16
Mega Marsh €14
Grey Heron €14

HASH p/g
Tashar Amber €12
Pebble Frost€11
Lime Dunes €14
Ash Petal €10

Target Market(s)

tourist in Amsterdam

Requirements
Nice to have
• cannabis sign leaf
• No Cigarettes allowed symbol

```html
<!DOCTYPE html>
<html lang="en">
<head>
<meta charset="utf-8">
<title>Coffeeshop Menu</title>
<link rel="stylesheet" href="https://fonts.googleapis.com/css2?family=Chewy&display=swap">
<style>
  :root {
    --band: #2e2e2e;
    --leaf-dark: #0f1a0c;
    --leaf-mid: #24381c;
    --leaf-light: #3a5530;
    --ink: #ffffff;
  }
  html, body {
    margin: 0;
    padding: 0;
    width: 1200px;
    height: 2884px;
    overflow: hidden;
    background: var(--leaf-dark);
  }
  .menu {
    position: relative;
    width: 1200px;
    height: 2884px;
    overflow: hidden;
    font-family: "Chewy", cursive;
    color: var(--ink);
  }
  .leaf-backdrop {
    position: absolute;
    inset: 0;
    background:
      radial-gradient(ellipse 70% 30% at 70% 25%, var(--leaf-light) 0%, transparent 70%),
      radial-gradient(ellipse 60% 25% at 30% 60%, var(--leaf-mid) 0%, transparent 70%),
      radial-gradient(ellipse 70% 30% at 65% 88%, var(--leaf-mid) 0%, transparent 70%),
      linear-gradient(180deg, var(--leaf-mid) 0%, var(--leaf-dark) 45%, var(--leaf-mid) 75%, var(--leaf-dark) 100%);
  }
  .title-band {
    position: absolute;
    left: 0;
    top: 0;
    width: 1200px;
    height: 346px;
    background: var(--band);
  }
  .title {
    position: absolute;
    left: 70px;
    top: 28px;
    margin: 0;
    font-size: 290px;
    line-height: 1;
    font-weight: 400;
    letter-spacing: 6px;
  }
  .section-head {
    position: absolute;
    left: 73px;
    margin: 0;
    font-size: 175px;
    line-height: 1;
    font-weight: 400;
  }
  .section-head .unit {
    font-size: 95px;
  }
  .item {
    position: absolute;
    left: 73px;
    margin: 0;
    font-size: 104px;
    line-height: 1;
    white-space: nowrap;
  }
  .weed-head { top: 560px; }
  .hash-head { top: 1880px; }
</style>
</head>
<body>
  <main class="menu">
    <div class="leaf-backdrop" role="img" aria-label="Dark green background of cannabis leaves"></div>
    <header class="title-band">
      <h1 class="title">MENU</h1>
    </header>

    <section class="weed">
      <h2 class="section-head weed-head">Weed <span class="unit">(p/g)</span></h2>
      <p class="item" style="top:790px">Oblivane €16</p>
      <p class="item" style="top:900px">Cloudplum €14</p>
      <p class="item" style="top:1010px">Tide Runner €14</p>
      <p class="item" style="top:1128px">Quincefig €16</p>
      <p class="item" style="top:1234px">Mega Marsh €14</p>
      <p class="item" style="top:1344px">Grey Heron €14</p>
    </section>

    <section class="hash">
      <h2 class="section-head hash-head">Hash <span class="unit">(p/g)</span></h2>
      <p class="item" style="top:2076px">Tashar Amber €12</p>
      <p class="item" style="top:2186px">Pebble Frost €11</p>
      <p class="item" style="top:2300px">Lime Dunes €14</p>
      <p class="item" style="top:2410px">Ash Petal €10</p>
    </section>
  </main>
</body>
</html>
```